Flag Order

We were just looking to order some branding flags to put on our rental equipment for our business. We would like different examples of the colors, shapes, sizes, backgrounds etc. Was thinking of just doing the plains icon instead of the whole logo on there. but open to ideas. preferably not a white background as they could get dirty,

```html
<!DOCTYPE html>
<html lang="en">
<head>
<meta charset="utf-8">
<title>Ridgeway Equipment Flag</title>
<link rel="stylesheet" href="https://fonts.googleapis.com/css2?family=Montserrat:wght@800&display=swap">
<style>
  :root {
    --backdrop: #4e4e4e;
    --flag-charcoal: #2c2c2c;
    --accent-blue: #1395e4;
    --mark-white: #ffffff;
  }
  html, body {
    margin: 0;
    padding: 0;
    overflow: hidden;
  }
  .canvas {
    width: 1200px;
    height: 1200px;
    background: var(--backdrop);
    position: relative;
    overflow: hidden;
  }
  .flag {
    position: absolute;
    left: 400px;
    top: 44px;
    width: 400px;
    height: 1113px;
    background: var(--flag-charcoal);
    overflow: hidden;
  }
  .flag-brand {
    position: absolute;
    left: 0;
    right: 0;
    top: 520px;
    display: flex;
    flex-direction: column;
    align-items: center;
    gap: 22px;
  }
  .brand-square {
    width: 44px;
    height: 44px;
    background: var(--accent-blue);
  }
  .brand-name {
    font-family: 'Montserrat', sans-serif;
    font-weight: 800;
    font-size: 50px;
    letter-spacing: 1px;
    color: var(--mark-white);
    margin: 0;
  }
  .corner-stripes {
    position: absolute;
    left: 0;
    top: 0;
    width: 400px;
    height: 1113px;
  }
  .stripe-blue { fill: var(--accent-blue); }
  .stripe-white { fill: var(--mark-white); }
</style>
</head>
<body>
  <main class="canvas">
    <section class="flag" aria-label="Ridgeway equipment flag">
      <div class="flag-brand">
        <span class="brand-square" aria-hidden="true"></span>
        <p class="brand-name">RIDGEWAY</p>
      </div>
      <svg class="corner-stripes" viewBox="0 0 400 1113" aria-hidden="true">
        <polygon class="stripe-blue" points="244,1113 400,935 400,985 288,1113"/>
        <polygon class="stripe-white" points="340,1113 400,1045 400,1113"/>
      </svg>
    </section>
  </main>
</body>
</html>
```